Business Cards Needed for Innovative Healthcare Marketing Company

We are a marketing company focused on healthcare. Our company is all about rebranding yourself renewing your image and generating results. The phoenix stands for "reborn" or "rising" which we provide new brands for our clients we take their old brands and renew it with creativity and innovation. I am looking for a business card with color dimension. I have attached an example of a card I think has the look and feel of what I am trying to accomplish. I like that the card example has black and grey font colors, I like the font placement and the small logo, I really like the use of the colors on the right those are the colors of my logo. My logo is phoenix so maybe incorporating flames similar to that design. I would like the back a solid color maybe red with an opaque version of the logo and website. As a marketing company I am always open to creative liberty!

Target Market(s)

Doctors and business professionals.

Industry/Entity Type

Marketing

Contact Information for Business Card

Valcorne Health Care Marketing
Marla Tenwick- CEO
#(512)638-2974
email-marla@valcorne.com
website- valcorne.com

Font styles to use
Sans Serif

Colors
ec1f27
f37122
ffc214
fbed22
fbf289
f04a50

Requirements
Must have
• The logo and required information
Nice to have
• icons by the information
Should not have
• child like font

```html
<!DOCTYPE html>
<html lang="en">
<head>
<meta charset="utf-8">
<title>Valcorne Health Care Marketing – Business Cards</title>
<link rel="stylesheet" href="https://fonts.googleapis.com/css2?family=Arvo:wght@400;700&family=Raleway:wght@200;300;400&display=swap">
<style>
  :root {
    --stage: #e9e6e2;
    --wine-light: #86303b;
    --wine: #6a1621;
    --wine-dark: #2a060b;
    --brand-red: #b5282b;
    --flame-orange: #f4854a;
    --flame-yellow: #ffc80a;
    --rim-grey: #5d5d61;
    --ink: #2b2b2b;
    --muted: #8a8a8a;
    --paper: #ffffff;
  }
  * { box-sizing: border-box; margin: 0; padding: 0; }
  html, body { width: 1200px; height: 913px; overflow: hidden; }
  body { background: var(--stage); position: relative; font-family: "Raleway", sans-serif; }

  .card {
    position: absolute;
    width: 560px; height: 320px;
    overflow: hidden;
    box-shadow: 0 14px 30px rgba(0,0,0,.25);
  }

  /* Back of card */
  .card-back {
    left: 60px; top: 90px;
    background: radial-gradient(ellipse at 65% 10%, var(--wine-light) 0%, var(--wine) 40%, var(--wine-dark) 100%);
  }
  .card-back .emblem-circle {
    position: absolute; left: 60px; top: 90px;
    width: 150px; height: 150px; border-radius: 50%;
    background: rgba(0,0,0,.35);
  }
  .card-back .brand-block { position: absolute; left: 240px; top: 92px; width: 280px; }
  .card-back .brand-name {
    font-family: "Raleway", sans-serif; font-weight: 200;
    font-size: 52px; letter-spacing: 2px; color: var(--paper); line-height: 1;
  }
  .card-back .brand-rule { height: 1px; background: rgba(255,255,255,.7); margin: 8px 0 6px; }
  .card-back .brand-tagline {
    font-weight: 300; font-size: 14.5px; letter-spacing: 1.5px; color: #e8dcdc;
  }
  .card-back .website {
    position: absolute; left: 300px; top: 228px;
    font-family: "Arvo", serif; font-size: 19px; color: #d4c6c8;
  }
  .card-back .website .accent { color: var(--brand-red); }

  /* Front of card */
  .card-front { left: 580px; top: 500px; background: var(--paper); }
  .card-front .flames { position: absolute; inset: 0; }
  .card-front .mini-brand { position: absolute; left: 40px; top: 42px; display: flex; align-items: center; gap: 10px; }
  .card-front .mini-brand .mark { width: 34px; height: 34px; border-radius: 50%; background: var(--flame-orange); }
  .card-front .mini-brand .name {
    font-family: "Raleway", sans-serif; font-weight: 400; font-size: 20px;
    letter-spacing: 1px; color: var(--brand-red); line-height: 1;
  }
  .card-front .mini-brand .tag {
    font-family: "Raleway", sans-serif; font-size: 7px; letter-spacing: .8px;
    color: var(--brand-red); border-top: 1px solid var(--brand-red); margin-top: 3px; padding-top: 2px;
  }
  .card-front .person { position: absolute; left: 40px; top: 130px; }
  .card-front .person-name {
    font-family: "Arvo", serif; font-weight: 700; font-size: 24px; color: var(--brand-red);
  }
  .card-front .person-role { font-family: "Arvo", serif; font-size: 16px; color: var(--muted); }
  .card-front .contacts { position: absolute; left: 40px; top: 212px; list-style: none; }
  .card-front .contacts li {
    display: flex; align-items: center; gap: 10px; height: 26px;
    font-family: "Arvo", serif; font-size: 15px; color: var(--ink);
  }
  .card-front .contacts svg { width: 18px; height: 18px; flex: none; }
</style>
</head>
<body>

<section class="card card-back" aria-label="Business card back">
  <div class="emblem-circle"></div>
  <div class="brand-block">
    <div class="brand-name">VALCORNE</div>
    <div class="brand-rule"></div>
    <div class="brand-tagline">HEALTHCARE MARKETING</div>
  </div>
  <div class="website">www.<span class="accent">valcorne</span>.com</div>
</section>

<section class="card card-front" aria-label="Business card front">
  <svg class="flames" viewBox="0 0 560 320" preserveAspectRatio="none" aria-hidden="true">
    <circle cx="580" cy="200" r="250" fill="var(--flame-yellow)" stroke="var(--rim-grey)" stroke-width="6"/>
    <circle cx="440" cy="-70" r="200" fill="var(--flame-orange)" stroke="var(--rim-grey)" stroke-width="6"/>
    <circle cx="620" cy="410" r="210" fill="var(--flame-orange)" stroke="var(--rim-grey)" stroke-width="6"/>
  </svg>

  <div class="mini-brand">
    <div class="mark"></div>
    <div>
      <div class="name">VALCORNE</div>
      <div class="tag">HEALTHCARE MARKETING</div>
    </div>
  </div>

  <div class="person">
    <div class="person-name">Marla TENWICK</div>
    <div class="person-role">CEO</div>
  </div>

  <ul class="contacts">
    <li>
      <svg viewBox="0 0 20 20"><circle cx="10" cy="10" r="10" fill="var(--brand-red)"/><path d="M6.5 5.5l2 2-1 1.3c.8 1.6 2 2.8 3.7 3.7l1.3-1 2 2-1.3 1.5C9.6 14.7 5.3 10.4 5 6.8z" fill="#fff"/></svg>
      (512)638-2974
    </li>
    <li>
      <svg viewBox="0 0 20 20"><circle cx="10" cy="10" r="10" fill="var(--brand-red)"/><rect x="5" y="6.5" width="10" height="7" fill="#fff"/><path d="M5 6.5l5 4 5-4" fill="none" stroke="var(--brand-red)" stroke-width="1"/></svg>
      marla@valcorne.com
    </li>
    <li>
      <svg viewBox="0 0 20 20"><circle cx="10" cy="10" r="10" fill="var(--brand-red)"/><circle cx="10" cy="10" r="5.5" fill="none" stroke="#fff" stroke-width="1.2"/><path d="M4.5 10h11M10 4.5c-2.5 3-2.5 8 0 11M10 4.5c2.5 3 2.5 8 0 11" fill="none" stroke="#fff" stroke-width="1"/></svg>
      valcorne.com
    </li>
  </ul>
</section>

</body>
</html>
```